Need a website where people can find information about the newly formed Northmere Valuation Oversight Board. Soon after, we will need a place to publish our findings as we audit each municipality in the State of Wisconsin. I have a logo (designed by Artwell Hub), a MS Word document showing the content and a set of images to choose from that we can purchase from Pixmarla.com (found here https://www.pixmarla.com/collaboration/boards/-Xq7TbLwRmNoPzYkAuH-Jd)

```html
<!DOCTYPE html>
<html lang="en">
<head>
<meta charset="utf-8">
<title>NVOB Recommendations for Legislators</title>
<link href="https://fonts.googleapis.com/css2?family=Roboto:wght@300;400;500;700&family=Work+Sans:wght@700;800&display=swap" rel="stylesheet">
<style>
  :root {
    --hero-grey: #bdbdbd;
    --brand-green: #3f8a14;
    --deep-green: #2f6410;
    --ink: #111111;
    --body-text: #555555;
    --white: #ffffff;
    --rule: #3a3a3a;
  }
  * { margin: 0; padding: 0; box-sizing: border-box; }
  html, body { width: 862px; height: 1200px; overflow: hidden; background: var(--white); }
  body { position: relative; font-family: "Roboto", sans-serif; color: var(--body-text); }

  .hero-shape { position: absolute; left: 0; top: 0; }
  .brand-mark {
    position: absolute; left: 80px; top: 30px;
    font: 700 20px "Work Sans", sans-serif; color: var(--brand-green); letter-spacing: 1px;
  }
  .hero-name {
    position: absolute; left: 0; width: 862px; top: 150px; text-align: center;
    font: 700 72px "Work Sans", sans-serif; color: var(--deep-green); letter-spacing: 3px;
  }
  .main-nav { position: absolute; top: 40px; left: 380px; display: flex; }
  .main-nav a {
    font: 500 10.5px "Roboto", sans-serif; color: var(--white); text-decoration: none;
    text-transform: uppercase; margin-right: 22px; padding-bottom: 5px; position: relative;
  }
  .main-nav a.is-active { border-bottom: 1.5px solid var(--white); }

  .scroll-ring {
    position: absolute; left: 390px; top: 283px; width: 82px; height: 82px;
    border-radius: 50%; border: 1px solid var(--white);
  }
  .scroll-button {
    position: absolute; left: 408px; top: 301px; width: 46px; height: 46px;
    border-radius: 50%; background: var(--white); box-shadow: 0 3px 8px rgba(0,0,0,.2);
    display: flex; align-items: center; justify-content: center;
  }

  .page-title {
    position: absolute; top: 392px; left: 0; width: 862px; text-align: center;
    font: 700 22px/31px "Work Sans", sans-serif; color: var(--ink); letter-spacing: .3px;
  }
  .intro { position: absolute; left: 80px; width: 702px; top: 472px; text-align: center;
    font: 300 11.2px/18.5px "Roboto", sans-serif; }
  .intro p { margin-bottom: 15.5px; }
  .intro p.lead-in { margin-top: 0; }

  .action-card {
    position: absolute; left: 108px; top: 678px; width: 646px; height: 278px;
    background: var(--white); border-radius: 6px; box-shadow: 0 2px 14px rgba(0,0,0,.08);
    padding: 24px 20px 0 26px;
  }
  .action-list { list-style: none; }
  .action-list li {
    position: relative; padding-left: 24px; margin-bottom: 9.5px;
    font: 300 10.2px/16.6px "Roboto", sans-serif; color: #4a4a4a;
  }
  .action-list li svg { position: absolute; left: 0; top: 3px; }

  .footer-shape { position: absolute; left: 0; top: 1000px; }
  .footer-name {
    position: absolute; top: 1086px; left: 0; width: 862px; text-align: center;
    font: 700 24px "Work Sans", sans-serif; color: var(--white); letter-spacing: 2px;
  }
  .footer-rule { position: absolute; left: 80px; top: 1161px; width: 702px; height: 1px; background: var(--rule); }
  .footer-meta { position: absolute; top: 1173px; font: 400 10px "Roboto", sans-serif; color: var(--white); }
  .copyright { left: 352px; }
  .legal-links { left: 614px; }
</style>
</head>
<body>

<svg class="hero-shape" width="862" height="340" viewBox="0 0 862 340" aria-hidden="true">
  <path d="M0 0H862V223Q431 439 0 223Z" fill="var(--brand-green)"/>
  <path d="M0 0H862V219Q431 413 0 219Z" fill="var(--hero-grey)"/>
</svg>

<div class="brand-mark">NVOB</div>
<div class="hero-name">NVOB</div>

<nav class="main-nav">
  <a href="#">Home</a>
  <a href="#">Audit Results</a>
  <a href="#" class="is-active">Recommendations</a>
  <a href="#">Blog</a>
  <a href="#">Contact Us</a>
</nav>

<div class="scroll-ring"></div>
<div class="scroll-button">
  <svg width="16" height="16" viewBox="0 0 16 16" aria-hidden="true">
    <path d="M8 2V13M3 8.5L8 13.5 13 8.5" fill="none" stroke="var(--brand-green)" stroke-width="2.6" stroke-linecap="round" stroke-linejoin="round"/>
  </svg>
</div>

<h1 class="page-title">NVOB RECOMMENDATIONS<br>FOR LEGISLATORS</h1>

<section class="intro">
  <p>Lorem ipsum dolor sit amet, consectetur adipiscing elit, sed do eiusmod tempor incididunt ut labore et dolore magna aliqua. Ut enim ad minim veniam, quis nostrud exercitation ullamco laboris nisi ut aliquip ex ea commodo consequat. Duis aute irure dolor in reprehenderit in voluptate velit esse cillum dolore eu fugiat nulla pariatur. Excepteur sint occaecat cupidatat non proident, sunt in culpa qui officia deserunt mollit anim id est laborum. Sed ut perspiciatis unde omnis iste natus error sit voluptatem accusantiumea.</p>
  <p>Excepteur sint occaecat cupidatat non proident, sunt in culpa qui officia deserunt mollit anim id est laborum. Sed ut perspiciatis unde omnis iste natus error sit voluptatem accusantium doloremque laudantium, totam rem aperiam, eaque ipsa quae ab illo inventore veritatis et quasi architecto beatae vitae dicta sunt explicabo nemo enim ipsam voluptatem quia voluptas sit as quia consea.</p>
  <p class="lead-in">The State Legislators need to do the following:</p>
</section>

<section class="action-card">
  <ul class="action-list">
    <li><svg width="10" height="10" viewBox="0 0 10 10"><circle cx="5" cy="5" r="5" fill="var(--brand-green)"/><path d="M2.6 5H7M5.2 3L7.2 5 5.2 7" fill="none" stroke="#fff" stroke-width="1.4"/></svg>Require the DOR to provide evidence each year that property tax rolls statewide are uniform.</li>
    <li><svg width="10" height="10" viewBox="0 0 10 10"><circle cx="5" cy="5" r="5" fill="var(--brand-green)"/><path d="M2.6 5H7M5.2 3L7.2 5 5.2 7" fill="none" stroke="#fff" stroke-width="1.4"/></svg>Come up with a better way to hold municipalities accountable for producing non-uniform property tax rolls.&nbsp; Current methods are outdated and have never actually been used (see Wisconsin Statute 73.03(3)).</li>
    <li><svg width="10" height="10" viewBox="0 0 10 10"><circle cx="5" cy="5" r="5" fill="var(--brand-green)"/><path d="M2.6 5H7M5.2 3L7.2 5 5.2 7" fill="none" stroke="#fff" stroke-width="1.4"/></svg>Pass a new law that overturns Halvorsen v. Brookdale 173 N.W.2d 627, 45 Wis.2d 683.&nbsp; This is bad case law which is used to justify sale chasing which results in non-uniform taxation.</li>
    <li><svg width="10" height="10" viewBox="0 0 10 10"><circle cx="5" cy="5" r="5" fill="var(--brand-green)"/><path d="M2.6 5H7M5.2 3L7.2 5 5.2 7" fill="none" stroke="#fff" stroke-width="1.4"/></svg>Pass a new law to ensure that similar properties are valued using the same valuation method.&nbsp; Using different valuation methods for similar properties makes no sense.</li>
    <li><svg width="10" height="10" viewBox="0 0 10 10"><circle cx="5" cy="5" r="5" fill="var(--brand-green)"/><path d="M2.6 5H7M5.2 3L7.2 5 5.2 7" fill="none" stroke="#fff" stroke-width="1.4"/></svg>Pass a new law to ensure that assessors can collect accurate data about each property.&nbsp; Property taxes will never be just and equitable if the data the assessor is using is inaccurate.</li>
    <li><svg width="10" height="10" viewBox="0 0 10 10"><circle cx="5" cy="5" r="5" fill="var(--brand-green)"/><path d="M2.6 5H7M5.2 3L7.2 5 5.2 7" fill="none" stroke="#fff" stroke-width="1.4"/></svg>Make sure municipal governments have the funds to do the job correctly.&nbsp; Choosing between fixing streets and just and equitable taxation is not a good idea.&nbsp; Lack of funding is not an excuse that the State Constitution allows for.</li>
  </ul>
</section>

<svg class="footer-shape" width="862" height="200" viewBox="0 0 862 200" aria-hidden="true">
  <path d="M0 121Q431 -93 862 121V200H0Z" fill="var(--brand-green)"/>
  <path d="M0 127Q431 -71 862 127V200H0Z" fill="var(--ink)"/>
</svg>

<div class="footer-name">NVOB</div>
<div class="footer-rule"></div>
<div class="footer-meta copyright">© 2022 NVOB &nbsp;|&nbsp; All Rights Reserved</div>
<div class="footer-meta legal-links">Privacy Policy &nbsp;&nbsp;|&nbsp;&nbsp; Terms &amp; Conditions</div>

</body>
</html>
```